Upscale business cards needed for Board of Directors

We need professional business cards created for members of our family business Board of Directors. We would like these relatively simple and straightforward, but also with a unique element to set them apart. Probably stick with neutral and simple colors - white, grey etc. We need space for the traditional elements, including name, title, address, email/phone number. And we will be creating several from this template so it needs to be template that is easy to switch information in and out of.
Business
See description

```html
<!DOCTYPE html>
<html lang="en">
<head>
<meta charset="utf-8">
<title>Harbourline Holdings – Business Card</title>
<link rel="stylesheet" href="https://fonts.googleapis.com/css2?family=Roboto:wght@400;500;700;900&display=swap">
<style>
  :root {
    --stage: #3a3a3a;
    --gold: #b7a275;
    --gold-line: #c9b68c;
    --ink: #1c1a19;
    --text: #2a2a2a;
    --muted: #555555;
    --paper: #ffffff;
  }
  * { box-sizing: border-box; margin: 0; padding: 0; }
  html, body {
    width: 1200px; height: 950px; overflow: hidden;
    background: var(--stage);
    font-family: "Roboto", Arial, sans-serif;
  }
  .card {
    position: absolute; left: 250px;
    width: 700px; height: 400px;
    box-shadow: 0 12px 30px rgba(0,0,0,.45);
    overflow: hidden;
  }
  .card--front { top: 45px; background: var(--gold); }
  .card--back { top: 505px; background: var(--paper); }

  .wordmark {
    font-weight: 900; text-transform: uppercase; line-height: 1;
    text-align: center;
  }
  .wordmark__main { display: block; letter-spacing: 1px; }
  .wordmark__sub { display: block; letter-spacing: 9px; }

  .card--front .wordmark {
    position: absolute; left: 0; right: 0; top: 150px; color: var(--paper);
  }
  .card--front .wordmark__main { font-size: 52px; }
  .card--front .wordmark__sub { font-size: 22px; margin-top: 6px; }

  .card--back .wordmark {
    position: absolute; right: 70px; top: 62px; color: var(--ink);
  }
  .card--back .wordmark__main { font-size: 40px; }
  .card--back .wordmark__sub { font-size: 17px; margin-top: 5px; }

  .address {
    position: absolute; right: 42px; top: 158px;
    text-align: right; font-size: 14px; line-height: 1.4; color: var(--muted);
  }
  .divider {
    position: absolute; left: 0; right: 0; top: 212px;
    height: 1.5px; background: var(--gold-line);
  }
  .person { position: absolute; left: 36px; top: 236px; }
  .person__name { font-size: 22px; font-weight: 500; color: var(--ink); }
  .person__title { font-size: 15px; color: var(--gold); margin-top: 2px; }
  .contact { list-style: none; margin-top: 14px; font-size: 15px; color: var(--muted); }
  .contact li { display: flex; align-items: center; gap: 12px; height: 22px; }
  .contact svg { width: 14px; height: 14px; fill: var(--ink); }

  .web-band {
    position: absolute; left: 300px; right: 0; top: 300px; height: 46px;
    background: var(--ink); color: var(--paper);
    display: flex; align-items: center; justify-content: center;
    font-size: 15px; letter-spacing: 6px; font-weight: 500;
  }
  .edge-gold { position: absolute; left: 0; right: 0; top: 356px; height: 4px; background: var(--gold); }
  .edge-ink { position: absolute; left: 0; right: 0; top: 366px; height: 10px; background: var(--ink); }
</style>
</head>
<body>
  <section class="card card--front">
    <div class="wordmark">
      <span class="wordmark__main">Harbourline</span>
      <span class="wordmark__sub">Holdings</span>
    </div>
  </section>

  <section class="card card--back">
    <div class="wordmark">
      <span class="wordmark__main">Harbourline</span>
      <span class="wordmark__sub">Holdings</span>
    </div>
    <address class="address">2170 Lindenwood Avenue<br>Cedar Grove, NY 10012</address>
    <div class="divider"></div>
    <div class="person">
      <p class="person__name">Mark Ellison</p>
      <p class="person__title">President</p>
      <ul class="contact">
        <li>
          <svg viewBox="0 0 24 24" aria-hidden="true"><path d="M6.6 10.8a15.1 15.1 0 0 0 6.6 6.6l2.2-2.2a1 1 0 0 1 1-.25 11.4 11.4 0 0 0 3.6.57 1 1 0 0 1 1 1V20a1 1 0 0 1-1 1A17 17 0 0 1 3 4a1 1 0 0 1 1-1h3.5a1 1 0 0 1 1 1c0 1.25.2 2.45.57 3.57a1 1 0 0 1-.25 1z"/></svg>
          555 0142 7788
        </li>
        <li>
          <svg viewBox="0 0 24 24" aria-hidden="true"><path d="M2 5h20v14H2z M2 5l10 8 10-8" fill="var(--ink)" stroke="var(--paper)" stroke-width="1.5"/></svg>
          mark@harbourline.com
        </li>
      </ul>
    </div>
    <div class="web-band">www.harbourline.com</div>
    <div class="edge-gold"></div>
    <div class="edge-ink"></div>
  </section>
</body>
</html>
```